International Petrochemical business needs a web design for Clearway Desk system

We need a web design for a "Clearway Desk" system for an international petrochemical company. The web site is used internally within the company. It is hosted by an internal department which provides government permit request service for other departments.

We would like to see designs of two pages using color light blue. (home page, internal page as attached).
Home Page:
1. Header has a background image and small animation. Header on home page can be taller than the header of the internal page.
2. Layout as attached.

Internal Page:
1. Header can use the same background image as the home page and can be shorter to utilize the page for content.
2. The blue icon behind every captions represent an icon. When user move mouse over this icon, it displays the caption in Thai language as a tooltip. This icon needs to be redesign.

The final design should communicate the followings:
- Excellent service provided system in terms of time and accurary
- Rapid growth of business via building petrochemical refinery plant
Updates

For Internal Page, the blue circle behind every captions represent an icon. When mouse over this icon, a tool tip showing the caption in Thai language is shown. Please also design this icon..

There are more feedbacks from customer as followed:

1. Banner should consists of 
    1.1 "Approved" stamp on paper
    1.2 An image of Garuda. It is used on every government documents in Thailand
    1.3 Image of petrochemical plant
2. Each menu item (Home, Permit, Search, etc) should have different colors. Drop down menu will use the same color as its parent menu item.
3. Overall tone of the web page should be light blue with background of the body the web page in white
4. "New Request" button should use green color with icon on it
5. Table header of each box in the body of the page should use dark blue background with text in white

Please kindly submit your revisions.
Thank you.

Industry/Entity Type

Business

Requirements
Must have
• 1. Design for 1024x768 screen resolution
2. Use light blue theme
3. Background of header where the company logo is must have white background

```html
<!DOCTYPE html>
<html lang="en">
<head>
<meta charset="utf-8">
<title>Clearway Desk</title>
<link href="https://fonts.googleapis.com/css2?family=Roboto:wght@400;500;700;900&family=Sarabun:wght@400&display=swap" rel="stylesheet">
<style>
  :root{
    --sky:#1fa3e0;
    --nav-top:#8fd0f2;
    --nav-bottom:#4fb1e6;
    --head-top:#43aee9;
    --head-bottom:#1d8fd5;
    --fold:#93cdf0;
    --panel-bg:#d7eefb;
    --divider:#9ccbe6;
    --ink:#1e2226;
    --link:#2f74c9;
    --pager:#2f98d6;
    --drop-bg:rgba(215,232,244,.92);
    --footer-line:#0b3c5c;
    --white:#ffffff;
  }
  *{box-sizing:border-box;margin:0;padding:0}
  html,body{width:1101px;height:1200px;overflow:hidden;background:var(--white)}
  body{position:relative;font-family:"Roboto",sans-serif;color:var(--ink)}

  .masthead{position:absolute;left:0;top:0;width:1101px;height:86px;background:var(--white)}
  .brand{position:absolute;left:78px;top:22px;display:flex;align-items:center;gap:10px}
  .brand-mark{width:38px;height:38px;border-radius:50%;background:var(--sky)}
  .brand-name{font-weight:700;font-size:17px;line-height:18px;color:var(--sky);width:150px}
  .site-title{position:absolute;left:336px;top:36px;font-size:38px;font-weight:700;color:var(--sky);letter-spacing:.5px}

  .main-nav{position:absolute;left:0;top:86px;width:1101px;height:46px;
    background:linear-gradient(var(--nav-top),var(--nav-bottom));display:flex;align-items:center;padding-left:99px}
  .main-nav a{color:var(--white);font-size:15px;text-decoration:none;text-shadow:0 1px 2px rgba(0,60,110,.5);text-transform:uppercase}
  .nav-sep{color:var(--white);font-size:15px;margin:0 14px;text-shadow:0 1px 2px rgba(0,60,110,.5)}
  .dropdown{position:absolute;left:176px;top:133px;width:142px;background:var(--drop-bg);padding:8px 0 4px}
  .dropdown a{display:block;font-size:12.5px;color:var(--ink);padding:0 12px;height:27px;line-height:20px;text-decoration:none}
  .dropdown-caret{position:absolute;left:242px;top:124px;width:0;height:0;border:8px solid transparent;border-bottom-color:var(--drop-bg)}

  .hero{position:absolute;left:0;top:132px;width:1101px;height:500px;
    background:linear-gradient(180deg,#7d97ad 0%,#9fb8cc 35%,#c3d7e6 65%,#ffffff 100%)}

  .panel{position:absolute;box-shadow:0 12px 14px -10px rgba(0,0,0,.35)}
  .panel-head{height:42px;position:relative;background:linear-gradient(var(--head-top),var(--head-bottom));
    clip-path:polygon(0 0,calc(100% - 34px) 0,100% 34px,100% 100%,0 100%);
    color:var(--white);font-size:19px;font-weight:500;padding:10px 14px;text-shadow:0 1px 1px rgba(0,50,100,.4)}
  .panel-fold{position:absolute;right:0;top:0;width:34px;height:34px;background:var(--fold);clip-path:polygon(0 0,100% 100%,0 100%)}
  .panel-body{background:var(--panel-bg);position:relative;padding:12px 0 0}
  .cols{display:grid;height:calc(100% - 34px)}
  .col{padding:0 14px;border-left:1px solid var(--divider)}
  .col:first-child{border-left:none}
  .col-title{font-size:17px;font-weight:500;line-height:20px;height:30px}
  .col-title.two-line{height:50px}
  .cell{font-size:12.5px;line-height:19.5px;height:19.5px;white-space:nowrap}
  .cell a{color:var(--link)}
  .cell.thai{font-family:"Sarabun",sans-serif}
  .dot{display:inline-block;width:14px;height:14px;border-radius:50%;vertical-align:-2px;margin-right:6px}
  .dot.late{background:#e22b1d}
  .dot.warn{background:#f2c31a}

  .pager{position:absolute;bottom:0;left:50%;transform:translateX(-50%);width:128px;height:22px;background:var(--pager);
    display:flex;align-items:center;justify-content:space-between;padding:0 8px;color:var(--white);font-size:11px}
  .pager svg{width:8px;height:12px}

  .new-request{position:absolute;left:572px;top:818px;width:490px;height:59px;border:1px solid #1a5f8c;
    background:linear-gradient(#7fcdf3,#2b9ad9 55%,#1f86c7);color:var(--white);font-size:23px;font-weight:700;
    display:flex;align-items:center;justify-content:center;text-shadow:0 1px 2px rgba(0,40,90,.5);
    box-shadow:0 12px 14px -10px rgba(0,0,0,.35)}

  .site-footer{position:absolute;left:0;top:1101px;width:1101px;height:99px;border-top:4px solid var(--footer-line);
    background:linear-gradient(#4fb2e6,#7fc9ef)}
  .copyright{position:absolute;left:80px;top:22px;font-size:9.5px;color:#10222f}
  .legal{position:absolute;right:60px;top:22px;font-size:9.5px;color:#10222f}
</style>
</head>
<body>
  <header class="masthead">
    <div class="brand"><span class="brand-mark"></span><span class="brand-name">NORVANE PETROCHEMICAL</span></div>
    <div class="site-title">CLEARWAY DESK</div>
  </header>

  <div class="hero" role="img" aria-label="Photograph of a petrochemical refinery plant with pipework, towers and yellow railings against a pale sky"></div>

  <nav class="main-nav">
    <a href="#">Home</a><span class="nav-sep">|</span>
    <a href="#">Permits</a><span class="nav-sep">|</span>
    <a href="#">Search</a><span class="nav-sep">|</span>
    <a href="#">Report</a><span class="nav-sep">|</span>
    <a href="#">Admin</a><span class="nav-sep">|</span>
    <a href="#">Help</a>
  </nav>
  <span class="dropdown-caret"></span>
  <div class="dropdown">
    <a href="#">Create New Permit</a>
    <a href="#">Transfer Role</a>
    <a href="#">Transfer Res. Person</a>
  </div>

  <!-- New Requests -->
  <section class="panel" style="left:62px;top:409px;width:488px;height:204px">
    <div class="panel-head">New Requests</div><span class="panel-fold"></span>
    <div class="panel-body" style="height:162px">
      <div class="cols" style="grid-template-columns:1fr 1fr 1fr;height:110px">
        <div class="col"><div class="col-title">Request No.</div><div class="cell"><a href="#">56-0003</a></div><div class="cell"><a href="#">56-0004</a></div></div>
        <div class="col"><div class="col-title">Requested Date</div><div class="cell">20/4/2013</div><div class="cell">21/4/2013</div></div>
        <div class="col"><div class="col-title">Branch</div><div class="cell">GC1</div><div class="cell">GC2</div></div>
      </div>
      <div class="pager"><svg viewBox="0 0 8 12"><path d="M6 1 1 6l5 5" stroke="#fff" stroke-width="2" fill="none"/></svg><span>1</span><span>2</span><span>3</span><span>4</span><span>5</span><svg viewBox="0 0 8 12"><path d="M2 1l5 5-5 5" stroke="#fff" stroke-width="2" fill="none"/></svg></div>
    </div>
  </section>

  <!-- My Working Requests -->
  <section class="panel" style="left:574px;top:409px;width:488px;height:204px">
    <div class="panel-head">My Working Requests</div><span class="panel-fold"></span>
    <div class="panel-body" style="height:162px">
      <div class="cols" style="grid-template-columns:1fr 1fr 1fr;height:110px">
        <div class="col"><div class="col-title">Request No.</div><div class="cell"><a href="#">56-0003</a></div><div class="cell"><a href="#">56-0004</a></div><div class="cell"><a href="#">56-0005</a></div><div class="cell"><a href="#">56-0006</a></div></div>
        <div class="col"><div class="col-title">Requested Date</div><div class="cell">20/4/2013</div><div class="cell">21/4/2013</div><div class="cell">20/4/2013</div><div class="cell">21/4/2013</div></div>
        <div class="col"><div class="col-title">Status</div><div class="cell">Waiting for process</div><div class="cell">In progress</div><div class="cell">Incomplete document</div><div class="cell">Cancel requested</div></div>
      </div>
      <div class="pager"><svg viewBox="0 0 8 12"><path d="M6 1 1 6l5 5" stroke="#fff" stroke-width="2" fill="none"/></svg><span>1</span><span>2</span><span>3</span><span>4</span><span>5</span><svg viewBox="0 0 8 12"><path d="M2 1l5 5-5 5" stroke="#fff" stroke-width="2" fill="none"/></svg></div>
    </div>
  </section>

  <!-- Expiring Permits -->
  <section class="panel" style="left:62px;top:629px;width:1000px;height:173px">
    <div class="panel-head">Expiring Permits</div><span class="panel-fold"></span>
    <div class="panel-body" style="height:131px">
      <div class="cols" style="grid-template-columns:1fr 1fr 1fr 1fr 1fr 1fr;height:92px">
        <div class="col"><div class="col-title two-line">Permit No</div><div class="cell"><a href="#">AB56001</a></div><div class="cell"><a href="#">BIO5502</a></div></div>
        <div class="col"><div class="col-title two-line">Expire Date</div><div class="cell">25/3/2013</div><div class="cell">24/3/2013</div></div>
        <div class="col"><div class="col-title two-line">Permit Name</div><div class="cell">Permit Name ###10</div><div class="cell">Permit Name ###20</div></div>
        <div class="col"><div class="col-title two-line">Branch</div><div class="cell">GC1</div><div class="cell">GC2</div></div>
        <div class="col"><div class="col-title two-line">Required Time<br>(Day)</div><div class="cell">30</div><div class="cell">60</div></div>
        <div class="col"><div class="col-title two-line">Due Date</div><div class="cell"><span class="dot late"></span>-40</div><div class="cell"><span class="dot warn"></span>-15</div></div>
      </div>
      <div class="pager"><svg viewBox="0 0 8 12"><path d="M6 1 1 6l5 5" stroke="#fff" stroke-width="2" fill="none"/></svg><span>1</span><span>2</span><span>3</span><span>4</span><span>5</span><svg viewBox="0 0 8 12"><path d="M2 1l5 5-5 5" stroke="#fff" stroke-width="2" fill="none"/></svg></div>
    </div>
  </section>

  <!-- My In Progress Requests -->
  <section class="panel" style="left:62px;top:817px;width:488px;height:252px">
    <div class="panel-head">My In Progress Requests</div><span class="panel-fold"></span>
    <div class="panel-body" style="height:210px">
      <div class="cols" style="grid-template-columns:1fr 1fr 1fr;height:160px">
        <div class="col"><div class="col-title">Request No.</div><div class="cell"><a href="#">56-0001</a></div><div class="cell"><a href="#">56-0002</a></div></div>
        <div class="col"><div class="col-title">Requested Date</div><div class="cell">20/4/2013</div><div class="cell">21/4/2013</div></div>
        <div class="col"><div class="col-title">Status</div><div class="cell thai">ระหว่างดำเนินการ</div><div class="cell thai">รอดำเนินการ</div></div>
      </div>
      <div class="pager"><svg viewBox="0 0 8 12"><path d="M6 1 1 6l5 5" stroke="#fff" stroke-width="2" fill="none"/></svg><span>1</span><span>2</span><span>3</span><span>4</span><span>5</span><svg viewBox="0 0 8 12"><path d="M2 1l5 5-5 5" stroke="#fff" stroke-width="2" fill="none"/></svg></div>
    </div>
  </section>

  <a class="new-request">NEW REQUEST</a>

  <!-- Recent Completed Requests -->
  <section class="panel" style="left:574px;top:892px;width:488px;height:177px">
    <div class="panel-head">Recent Completed Requests</div><span class="panel-fold"></span>
    <div class="panel-body" style="height:135px">
      <div class="cols" style="grid-template-columns:1fr 1fr;height:100px">
        <div class="col"><div class="col-title">Request No.</div><div class="cell"><a href="#">55-0100</a></div><div class="cell"><a href="#">55-0088</a></div><div class="cell"><a href="#">55-0002</a></div></div>
        <div class="col"><div class="col-title">Completed Date</div><div class="cell">25/3/2013</div><div class="cell">24/3/2013</div><div class="cell">18/1/2013</div></div>
      </div>
      <div class="pager"><svg viewBox="0 0 8 12"><path d="M6 1 1 6l5 5" stroke="#fff" stroke-width="2" fill="none"/></svg><span>1</span><span>2</span><span>3</span><span>4</span><span>5</span><svg viewBox="0 0 8 12"><path d="M2 1l5 5-5 5" stroke="#fff" stroke-width="2" fill="none"/></svg></div>
    </div>
  </section>

  <footer class="site-footer" role="img" aria-label="Faint blue-toned photograph of refinery structures behind the footer">
    <div class="copyright">Copyright © 2013 NorvanePetrochemical. All rights reserved.</div>
    <div class="legal">Terms and Condition | Privacy</div>
  </footer>
</body>
</html>
```